Quanbrook Limited needs a business card design

We need a business card design that reflects both professionalism and innovation and captures our brand identity. We provide online enterprise solutions to HR and executive management. We would like to use the colors in our logo (Blue and Orange). See attached file.

We would like a more creative design than the existing attached business card but maintain the same information on it.

To see our products site, please visit www.quanbrook.example which reflects more our identity
Updates

Please see our site: www.quanbrook.example, not www.quanbrook.example.uk for our colors and look and feel

Target Market(s)

Senior Executives

Industry/Entity Type

Business

Requirements
Must have
• Logo and use of logo colors
Nice to have
• Icons
Should not have
• Images

```html
<!DOCTYPE html>
<html lang="en">
<head>
<meta charset="utf-8">
<title>Quanbrook Limited — Business Card</title>
<link href="https://fonts.googleapis.com/css2?family=Exo+2:wght@400;500;700&display=swap" rel="stylesheet">
<style>
  :root {
    --backdrop: #a3a3a3;
    --card: #ffffff;
    --brand-blue: #1447c0;
    --brand-orange: #e2531b;
    --ink: #2b2b2b;
    --divider: #d9d9d9;
  }
  * { margin: 0; padding: 0; box-sizing: border-box; }
  html, body {
    width: 1200px; height: 895px; overflow: hidden;
    background: var(--backdrop);
    font-family: "Exo 2", sans-serif;
  }
  .card {
    position: absolute;
    width: 600px; height: 340px;
    background: var(--card);
    box-shadow: 0 10px 24px rgba(0,0,0,.25);
    overflow: hidden;
  }
  .card--front { left: 560px; top: 70px; }
  .card--back { left: 60px; top: 470px; }
  .card__art { position: absolute; inset: 0; width: 100%; height: 100%; }

  .wordmark {
    position: absolute;
    display: flex; align-items: center; gap: 8px;
    color: var(--brand-blue);
    font-weight: 700;
    letter-spacing: -1px;
    line-height: 1;
  }
  .wordmark__dot {
    width: 14px; height: 14px; border-radius: 50%;
    background: var(--brand-orange);
  }
  .card--front .wordmark { left: 0; right: 0; top: 140px; justify-content: center; font-size: 66px; }
  .card--front .wordmark__dot { width: 18px; height: 18px; }
  .card--back .wordmark { left: 30px; top: 28px; font-size: 52px; }

  .person { position: absolute; right: 40px; top: 100px; text-align: left; }
  .person__name { color: var(--brand-blue); font-size: 19px; font-weight: 500; letter-spacing: 1px; }
  .person__role { color: var(--ink); font-size: 9px; letter-spacing: 1px; margin-top: 6px; }

  .contact { position: absolute; color: var(--ink); font-size: 14px; line-height: 1.45; letter-spacing: .5px; }
  .contact--web { left: 22px; top: 198px; }
  .contact--address { left: 228px; top: 218px; }
  .contact--phone { left: 430px; top: 234px; }
</style>
</head>
<body>

<section class="card card--front" aria-label="Card front">
  <svg class="card__art" viewBox="0 0 600 340" aria-hidden="true">
    <g fill="var(--brand-blue)">
      <polygon points="0,0 240,0 252,22 240,44 0,44"/>
      <polygon points="250,0 600,0 600,44 250,44 262,22"/>
      <polygon points="0,296 380,296 392,318 380,340 0,340"/>
      <polygon points="390,296 600,296 600,340 390,340 402,318"/>
    </g>
    <g fill="var(--divider)">
      <polygon points="0,44 252,44 246,52 0,52"/>
      <polygon points="0,288 380,288 386,296 0,296"/>
    </g>
  </svg>
  <div class="wordmark"><span>Quanbrook</span><span class="wordmark__dot"></span></div>
</section>

<section class="card card--back" aria-label="Card back">
  <svg class="card__art" viewBox="0 0 600 340" aria-hidden="true">
    <g fill="var(--brand-blue)">
      <polygon points="0,112 192,112 206,134 192,156 0,156"/>
      <polygon points="204,142 398,142 412,164 398,186 204,186 218,164"/>
      <polygon points="410,174 600,174 600,218 410,218 424,196"/>
      <rect x="0" y="298" width="600" height="42"/>
    </g>
    <g fill="none" stroke="var(--brand-orange)" stroke-width="3">
      <polyline points="196,142 210,164 196,186"/>
      <polyline points="402,174 416,196 402,218"/>
    </g>
    <rect x="0" y="290" width="600" height="3" fill="var(--brand-orange)"/>
    <g class="icon icon--globe" fill="none" stroke="#fff" stroke-width="1.6">
      <circle cx="34" cy="134" r="11"/>
      <ellipse cx="34" cy="134" rx="5" ry="11"/>
      <line x1="23" y1="134" x2="45" y2="134"/>
      <line x1="25" y1="128" x2="43" y2="128"/>
      <line x1="25" y1="140" x2="43" y2="140"/>
    </g>
    <path class="icon icon--pin" fill="#fff" d="M300,152 a9,9 0 0 1 9,9 c0,7 -9,16 -9,16 c0,0 -9,-9 -9,-16 a9,9 0 0 1 9,-9 z M300,157 a4,4 0 1 0 0.01,0 z" fill-rule="evenodd"/>
    <g class="icon icon--phone" fill="none" stroke="#fff" stroke-width="1.8">
      <rect x="553" y="183" width="14" height="25" rx="2"/>
      <line x1="557" y1="203" x2="563" y2="203"/>
    </g>
  </svg>
  <div class="wordmark"><span>Quanbrook</span><span class="wordmark__dot"></span></div>
  <div class="person">
    <div class="person__name">ALDO FENNICK</div>
    <div class="person__role">GRAPHICS DESIGNER</div>
  </div>
  <div class="contact contact--web">hello@quanbrook.example<br>www.quanbrook.example</div>
  <div class="contact contact--address">041 12th floor Court<br>Linden Road KVR</div>
  <div class="contact contact--phone">012 555 0142<br>012 555 0142</div>
</section>

</body>
</html>
```